Aunt Roula's Bakery

I am about to create a luxury boutique that specializes in cake baking and cupcake
and ready for parties and special events and order delivery
the logo has already made

Boutique

Email:auntroulasbakery@mailbox-example.net
Instagram: aunt_roula_bakery
Twitter: xxxxxxx
WhatsApp: xxxxxxx

Requirements
Must have
• luxury design

```html
<!DOCTYPE html>
<html lang="en">
<head>
<meta charset="utf-8">
<title>Aunt Roula's Bakery – Business Card</title>
<link rel="stylesheet" href="https://fonts.googleapis.com/css2?family=PT+Sans:wght@400;700&display=swap">
<style>
  :root {
    --backdrop: #3b3b3b;
    --pink: #d590a2;
    --pink-deep: #d07f93;
    --stone: #77736d;
    --paper: #f6f6f6;
    --ink: #4a4a4a;
  }
  * { box-sizing: border-box; margin: 0; padding: 0; }
  html, body { width: 1200px; height: 750px; overflow: hidden; }
  body {
    background: var(--backdrop);
    font-family: "PT Sans", sans-serif;
    position: relative;
  }
  .card {
    position: absolute;
    top: 228px;
    width: 461px;
    height: 262px;
    border-radius: 14px;
    overflow: hidden;
  }
  .card-front { left: 124px; }
  .card-back { left: 618px; background: var(--pink); }

  .front-curves { position: absolute; inset: 0; width: 100%; height: 100%; }

  .brand {
    position: absolute;
    left: 40px;
    top: 75px;
    width: 180px;
    text-align: center;
  }
  .brand-dot {
    width: 40px; height: 40px;
    border-radius: 50%;
    background: var(--pink);
    border: 3px solid var(--paper);
    box-shadow: 0 0 0 2px var(--pink);
    margin: 0 auto 8px;
  }
  .brand-name {
    color: var(--stone);
    font-size: 19px;
    font-weight: 400;
    line-height: 1.15;
    letter-spacing: 0.5px;
  }

  .divider {
    position: absolute;
    left: 226px; top: 72px;
    width: 1px; height: 122px;
    background: #c9c9c9;
  }

  .contact {
    position: absolute;
    left: 242px; top: 69px;
  }
  .person-name { color: var(--pink-deep); font-size: 16.5px; font-weight: 700; line-height: 20px; }
  .person-role { color: #777; font-size: 13px; line-height: 17px; margin-bottom: 3px; }
  .contact-list { list-style: none; }
  .contact-list li {
    display: flex; align-items: center;
    height: 17.6px;
    font-size: 11.2px;
    color: var(--ink);
  }
  .contact-icon { width: 12px; height: 12px; margin-right: 8px; flex: none; }
  .contact-dot {
    width: 11px; height: 11px; border-radius: 50%;
    background: var(--pink);
    margin: 0 9px 0 1px; flex: none;
  }

  .back-mark {
    position: absolute;
    left: 0; right: 0; top: 62px;
    text-align: center;
  }
  .back-ring {
    width: 84px; height: 84px;
    border-radius: 50%;
    border: 4px solid var(--stone);
    margin: 0 auto 12px;
  }
  .back-name { color: var(--stone); font-size: 18px; letter-spacing: 0.5px; }
  .web-address {
    position: absolute;
    left: 0; right: 0; top: 226px;
    text-align: center;
    color: var(--stone);
    font-size: 10.5px;
    letter-spacing: 1px;
  }
</style>
</head>
<body>

<section class="card card-front">
  <svg class="front-curves" viewBox="0 0 461 262" preserveAspectRatio="none" aria-hidden="true">
    <rect width="461" height="262" fill="var(--pink)"/>
    <path d="M0 24 Q235 -2 461 30 L461 44 Q235 10 0 32 Z" fill="var(--stone)"/>
    <path d="M0 31 Q235 10 461 44 L461 216 Q235 258 0 224 Z" fill="var(--paper)"/>
    <path d="M0 222 Q235 256 461 214 L461 222 Q235 272 0 236 Z" fill="var(--stone)"/>
    <path d="M0 237 Q235 273 461 223 L461 226 Q235 277 0 240 Z" fill="#ffffff"/>
  </svg>

  <div class="brand">
    <div class="brand-dot"></div>
    <div class="brand-name">Aunt Roula's<br>Bakery</div>
  </div>

  <div class="divider"></div>

  <div class="contact">
    <div class="person-name">Daniel Hart</div>
    <div class="person-role">CEO/Founder</div>
    <ul class="contact-list">
      <li>
        <svg class="contact-icon" viewBox="0 0 24 24"><path fill="var(--pink)" d="M6.6 10.8c1.4 2.8 3.8 5.1 6.6 6.6l2.2-2.2c.3-.3.7-.4 1-.2 1.1.4 2.3.6 3.6.6.6 0 1 .4 1 1V20c0 .6-.4 1-1 1C10.6 21 3 13.4 3 4c0-.6.4-1 1-1h3.5c.6 0 1 .4 1 1 0 1.3.2 2.5.6 3.6.1.3 0 .7-.2 1z"/></svg>
        555 014 2296
      </li>
      <li>
        <svg class="contact-icon" viewBox="0 0 24 24"><rect x="2" y="5" width="20" height="14" rx="1.5" fill="var(--pink)"/><path d="M3 6l9 7 9-7" fill="none" stroke="var(--paper)" stroke-width="1.8"/></svg>
        auntroulasbakery@mailbox-example.net
      </li>
      <li><span class="contact-dot"></span>aunt_roula_bakery</li>
      <li><span class="contact-dot"></span>auntroulasbakery</li>
      <li><span class="contact-dot"></span>auntroulasbakery</li>
    </ul>
  </div>
</section>

<section class="card card-back">
  <div class="back-mark">
    <div class="back-ring"></div>
    <div class="back-name">Aunt Roula's Bakery</div>
  </div>
  <div class="web-address">www.roulasbakery-example.com</div>
</section>

</body>
</html>
```